Business Card for Multi-Brand Sportswear Company

We are looking for a business card which represents our company and the multiple brands within it.

The company: Fen Athletics (LTD)
The brands: Fen, TavaPuni, ElmStretch, Grit and Rain

Employees using these cards would be representing Fen Athletics, rather than any of the individual brands. You will see a current design within the uploaded files, to give some inspiration. The actual text of the brands is not necessary, but the logos should be on there is some format.

Our creative minds on this are stretched, so we are looking for someone to make this their own, and show us what a good business card should look like.

We may like to get these printed with spot gloss, so keep that in mind with your designs.

www.fenathletics.co.uk

Industry/Entity Type

Business

Contact Information for Business Card

Leo Pemberton-Hale
Operations Manager
(+44) 1632 960 418
Leo@fenathletics.co.uk
www.fenathletics.co.uk

Font styles to use
Sans Serif
Other font styles liked:
• Eurostile

Colors
ffffff

Requirements
Nice to have
• Dark (black) background

```html
<!DOCTYPE html>
<html lang="en">
<head>
<meta charset="utf-8">
<title>Fen Athletics – Business Card</title>
<link rel="stylesheet" href="https://fonts.googleapis.com/css2?family=Michroma&family=Roboto:wght@400;500&display=swap">
<style>
  :root {
    --stage: #3a3f47;
    --card: #1c1c1d;
    --white: #ffffff;
    --silver: #b9bbbe;
    --muted: #6e7073;
    --red: #e3242b;
    --rule: #5a5b5d;
  }
  * { margin: 0; padding: 0; box-sizing: border-box; }
  html, body { width: 1200px; height: 900px; overflow: hidden; }
  body {
    background: var(--stage);
    display: flex; flex-direction: column; align-items: center; justify-content: center;
    gap: 48px;
    font-family: "Roboto", Arial, sans-serif;
  }
  .card {
    width: 640px; height: 372px;
    background: var(--card);
    position: relative;
    box-shadow: 0 10px 30px rgba(0,0,0,.35);
  }
  .card--front { transform: translateX(-90px); display: flex; flex-direction: column; align-items: center; justify-content: center; gap: 34px; }
  .card--back { transform: translateX(90px); }

  .company-name {
    font-family: "Michroma", Arial, sans-serif;
    font-size: 40px; color: var(--silver); letter-spacing: 1px;
    display: flex; align-items: center; gap: 16px;
  }
  .company-name .dot { width: 14px; height: 14px; border-radius: 50%; background: var(--silver); }
  .brand-row { display: flex; gap: 34px; list-style: none; }
  .brand-row li { font-family: "Michroma", Arial, sans-serif; font-size: 12px; color: var(--muted); }

  .identity {
    position: absolute; right: 246px; top: 128px; text-align: right;
  }
  .identity__name {
    font-family: "Michroma", Arial, sans-serif; font-weight: 400;
    font-size: 26px; color: var(--white); letter-spacing: .5px;
  }
  .identity__role { font-size: 17px; color: var(--red); margin-top: 4px; }
  .divider { position: absolute; left: 410px; top: 86px; width: 1px; height: 120px; background: var(--rule); }
  .contact { position: absolute; left: 430px; top: 98px; list-style: none; }
  .contact li { display: flex; align-items: center; gap: 12px; font-size: 13px; color: var(--white); height: 30px; }
  .contact svg { width: 14px; height: 14px; fill: var(--red); flex: none; }
  .contact .accent { color: var(--red); }
  .address {
    position: absolute; left: 0; right: 0; bottom: 52px;
    display: flex; justify-content: center; align-items: center; gap: 10px;
    font-size: 15px; color: var(--white); letter-spacing: .3px;
  }
  .address svg { width: 14px; height: 18px; fill: var(--red); }
</style>
</head>
<body>
  <section class="card card--front" aria-label="Card front">
    <div class="company-name"><span class="dot"></span>Fen Athletics</div>
    <ul class="brand-row">
      <li>Fen</li><li>TavaPuni</li><li>ElmStretch</li><li>Grit and Rain</li>
    </ul>
  </section>

  <section class="card card--back" aria-label="Card back">
    <div class="identity">
      <h1 class="identity__name">OWEN ASHCOMBE</h1>
      <p class="identity__role">Managing Director</p>
    </div>
    <div class="divider"></div>
    <ul class="contact">
      <li><svg viewBox="0 0 24 24"><path d="M6.6 10.8a15 15 0 0 0 6.6 6.6l2.2-2.2a1 1 0 0 1 1-.25 11.4 11.4 0 0 0 3.6.6 1 1 0 0 1 1 1V20a1 1 0 0 1-1 1A17 17 0 0 1 3 4a1 1 0 0 1 1-1h3.5a1 1 0 0 1 1 1c0 1.25.2 2.45.6 3.6a1 1 0 0 1-.25 1z"/></svg>+44(0)1632960418</li>
      <li><svg viewBox="0 0 24 24"><path d="M2 5h20v14H2z M2 5l10 8 10-8" stroke="#1c1c1d" stroke-width="1.5"/></svg>owen@fenathletics.co.uk</li>
      <li><svg viewBox="0 0 24 24"><circle cx="12" cy="12" r="10"/><path d="M2 12h20M12 2c3 3 3 17 0 20M12 2c-3 3-3 17 0 20" stroke="#1c1c1d" stroke-width="1.4" fill="none"/></svg>www.<span class="accent">fenathletics</span>.co.uk</li>
    </ul>
    <p class="address"><svg viewBox="0 0 14 18"><path d="M7 0a7 7 0 0 1 7 7c0 5-7 11-7 11S0 12 0 7a7 7 0 0 1 7-7zm0 4.5a2.5 2.5 0 1 0 0 5 2.5 2.5 0 0 0 0-5z"/></svg>Reed Lane, Marsholt, Fenby, FB124QX</p>
  </section>
</body>
</html>
```